Wordpress Design Project (Brookhollow)

We need a wordpress design for an established auction and real estate company based in New Hampshire. The winning design will incorporate the colors of logo (red and blue) creatively with black or gray in a very professional and clean layout. Client mentions liking the site http://www.pellandbids.example/ as a general idea.

Industry/Entity Type

Real Estate

Requirements
Must have
• Navigation:
1) Home (lorem text)
2) Upcoming Auctions
3) Auction Results
4) Sell or Consign
5) About Us
6) Services
7) FAQ
8) Contact Us

Site will have slideshow, initial image attached.
Sidebar widgets:
- Email sign up form
- Featured Auction (like at http://www.quillmarksales.example) - - - - Video Widget
- Testimonials widget

Footer will have smaller logo, contact info, and 2 association logos (attached)
-
Nice to have
• use of drop-down menu design for 'Services'
1) Appraisals
2) Consulting
Should not have
• please use no gavels in the design

```html
<!DOCTYPE html>
<html lang="en">
<head>
<meta charset="utf-8">
<title>Brookhollow Auctioneers</title>
<link rel="stylesheet" href="https://fonts.googleapis.com/css2?family=Open+Sans:wght@400;600;700&family=Arimo:wght@400;700&display=swap">
<style>
:root{
  --blue:#1b2a78;
  --blue-dark:#13205f;
  --red:#8e1322;
  --red-text:#9a1428;
  --ink:#1e1e1e;
  --gray-bg:#f4f4f5;
  --panel:#ececec;
  --line:#d3d3d3;
  --footer:#1b1b1b;
  --footer-bar:#262626;
}
*{box-sizing:border-box;margin:0;padding:0}
html,body{width:960px;height:1200px;overflow:hidden}
body{position:relative;background:var(--gray-bg);font-family:Arimo,Arial,sans-serif;color:var(--ink)}
.abs{position:absolute}
.header{left:0;top:0;width:960px;height:106px;background:linear-gradient(#f7f7f7,#ebebeb)}
.brand{left:100px;top:22px;display:flex;align-items:center;gap:9px}
.brand-mark{width:54px;height:54px;border-radius:50%;background:var(--blue)}
.brand-name{font-family:"Open Sans",sans-serif;font-size:20px;color:var(--blue);letter-spacing:.3px;margin-top:12px}
.phone{right:94px;top:26px;display:flex;align-items:center;gap:10px;font-family:"Open Sans",sans-serif;font-size:17px;color:var(--red)}
.connect{left:588px;top:74px;font-size:12px}
.social{left:698px;top:68px;display:flex;gap:8px}
.social span{width:27px;height:27px;border-radius:5px;display:block}
.redline{left:0;top:106px;width:960px;height:5px;background:var(--red)}
.nav{left:0;top:113px;width:960px;height:35px;background:linear-gradient(#24358f,var(--blue-dark));border-bottom:1px solid #0d1646}
.nav ul{list-style:none;display:flex;margin-left:82px;height:35px}
.nav li{font-family:"Open Sans",sans-serif;font-size:11.5px;font-weight:600;color:#fff;padding:0 19px;line-height:32px;border-right:1px solid #31428f;position:relative}
.nav li:last-child{border-right:0}
.nav li.has-sub::after{content:"";position:absolute;left:50%;bottom:4px;margin-left:-3px;border:3px solid transparent;border-top-color:#fff}
.hero{left:0;top:148px;width:960px;height:272px;background:linear-gradient(#dcdcdc,#c9c9c9)}
.slide-frame{left:81px;top:165px;width:550px;height:237px;background:#fff;padding:5px}
.slide{width:100%;height:100%;background:linear-gradient(135deg,#6d6558,#a89a83 45%,#4a4338)}
.signup{left:641px;top:165px;width:237px;height:237px;background:var(--red);color:#fff;padding:18px 18px}
.signup h3{font-family:"Open Sans",sans-serif;font-weight:400;font-size:18px;margin-bottom:18px}
.signup label{display:block;font-family:"Open Sans",sans-serif;font-size:10.5px;margin-bottom:8px;letter-spacing:.3px}
.signup .field{height:27px;border-radius:3px;background:linear-gradient(#e9e9e9,#d4d4d4);margin-bottom:22px}
.btn-sub{display:flex;align-items:center;gap:7px;width:136px;height:30px;border-radius:4px;background:linear-gradient(#fafafa,#d6d6d6);color:#333;font-weight:700;font-size:12.5px;padding-left:6px;margin-top:-1px}
.dropdown{left:536px;top:148px;width:126px;height:66px;background:var(--blue);padding:10px 4px 0;border-radius:0 0 3px 3px}
.dropdown div{font-family:"Open Sans",sans-serif;font-size:11.5px;color:#fff;padding:3px 14px;height:21px;margin-bottom:4px}
.dropdown .on{background:#eef0f6;color:var(--blue);border-radius:4px}
.sec-title{font-size:14px;font-weight:400;text-transform:uppercase;color:var(--red-text)}
.sec-title b{font-weight:400;color:var(--blue)}
.welcome-icon{left:81px;top:437px;width:30px;height:30px;border-radius:50%;background:var(--blue)}
.intro{left:82px;top:478px;width:520px;font-size:9.4px;line-height:14px}
.auction{left:81px;width:553px;background:linear-gradient(#fff,#e9e9e9);border:1px solid var(--line)}
.auction .bar{height:31px;background:linear-gradient(#2a3b93,var(--blue-dark));color:#fff;font-weight:700;font-size:12px;letter-spacing:.3px;padding:9px 13px}
.auction .thumb{position:absolute;left:15px;top:55px;width:120px;height:80px;border:1px solid #5a8fbf;background:linear-gradient(#9bb8d6,#d7dfe3 55%,#5f8a3c)}
.auction .info{position:absolute;left:151px;top:55px;width:380px;font-size:10.5px;line-height:12px}
.auction .info h4{color:var(--red-text);font-size:11px;letter-spacing:.2px;line-height:13.5px;margin-bottom:8px}
.auction .btn{position:absolute;left:14px;width:121px;height:30px;border-radius:5px;color:#fff;font-weight:700;font-size:13px;display:flex;align-items:center;gap:8px;padding-left:15px}
.btn.details{top:147px;background:linear-gradient(#a31a2c,var(--red))}
.btn.photos{top:181px;background:linear-gradient(#2a3b93,var(--blue-dark))}
.auction .dates{position:absolute;left:153px;top:155px;font-size:10.5px;line-height:14.5px}
.auction .dates b{color:var(--red-text);font-size:9.6px;display:block;margin-bottom:1px}
.video{left:644px;top:466px;width:235px;height:162px;background:linear-gradient(#e8e8e8,#c9c9c9)}
.video .play{position:absolute;left:93px;top:46px;width:53px;height:38px;background:#2d2d2d;border-radius:3px}
.video .ctrl{position:absolute;left:0;bottom:0;width:100%;height:15px;background:#111;color:#9a9a9a;font-size:7px;display:flex;align-items:center;justify-content:space-between;padding:0 8px}
.side-box{left:646px;width:232px;background:linear-gradient(#f7f7f7,#e8e8e8);border:1px solid var(--line)}
.side-box .bar{height:29px;background:linear-gradient(#2a3b93,var(--blue-dark));color:#fff;font-family:"Open Sans",sans-serif;padding:5px 17px;font-size:15.5px}
.featured p{font-size:9.5px;text-align:center;line-height:13.5px}
.red{color:var(--red-text)}
.featured .thumb{margin:18px auto 22px;width:134px;height:86px;border:1px solid #ccc;background:linear-gradient(#7fa9d8,#dfd8c8 55%,#6e8a52)}
.testi .bar{font-size:13.5px;padding-top:7px;padding-left:12px}
.testi blockquote{font-size:9.5px;line-height:12px;padding:16px 20px 0 23px;position:relative}
.footer{left:0;top:1068px;width:960px;height:104px;background:var(--footer);color:#fff}
.footer h5{position:absolute;left:83px;top:17px;font-weight:400;font-size:14px}
.footer address{position:absolute;left:83px;top:44px;font-style:normal;font-weight:700;font-size:10px;line-height:14px}
.badge-a{left:431px;top:1112px;width:40px;height:36px;background:#cfcfcf;border-radius:3px}
.badge-b{left:501px;top:1112px;width:136px;height:32px;background:#f2f2f2;border:2px solid #555}
.foot-brand{left:724px;top:1099px;display:flex;align-items:center;gap:7px}
.foot-brand .brand-mark{width:44px;height:44px;background:#d9d9d9}
.foot-brand .brand-name{color:#d9d9d9;font-size:15px;margin-top:6px}
.copy{left:0;top:1172px;width:960px;height:28px;background:var(--footer-bar);color:#ddd;font-size:9.8px;text-align:center;line-height:28px}
</style>
</head>
<body>
<header class="header abs">
  <div class="brand abs"><span class="brand-mark"></span><span class="brand-name">BROOKHOLLOW</span></div>
  <div class="phone abs">
    <svg width="10" height="20" viewBox="0 0 10 20"><path d="M8 1H4C2 1 1 3 1 10s1 9 3 9h4v-5H5c-.6-2-.6-6 0-8h3z" fill="#8e1322"/></svg>
    555 014 2290
  </div>
  <div class="connect abs">Stay Connected</div>
  <div class="social abs">
    <span style="background:#b8202a"></span><span style="background:#3a5a9a"></span><span style="background:#3a4a5a"></span><span style="background:#2a7fc0"></span><span style="background:#e8771f"></span>
  </div>
</header>
<div class="redline abs"></div>
<nav class="nav abs">
  <ul>
    <li>Home</li><li>Upcoming Auctions</li><li>Auction Results</li><li>Sell or Consign</li><li class="has-sub" style="padding:0 30px">Services</li><li>About Us</li><li style="padding:0 27px">FAQ</li><li>Contact Us</li>
  </ul>
</nav>
<section class="hero abs">
</section>
<div class="slide-frame abs"><div class="slide" role="img" aria-label="Slideshow photo of a display case of collectible coins"></div></div>
<form class="signup abs">
  <h3>Email sign-up</h3>
  <label>Your Name</label><div class="field"></div>
  <label>Your Email Address</label><div class="field"></div>
  <div class="btn-sub"><svg width="22" height="16" viewBox="0 0 22 16"><rect x="1" y="2" width="20" height="13" rx="1" fill="#333"/><path d="M1 2l10 8 10-8" stroke="#ddd" fill="none" stroke-width="1.3"/></svg>Subscribe Now</div>
</form>
<div class="dropdown abs"><div class="on">Appraisals</div><div>Consulting</div></div>

<div class="welcome-icon abs"></div>
<h2 class="sec-title abs" style="left:120px;top:446px">Welcome to <b>Brookhollow</b></h2>
<div class="intro abs">
  <p><b>Lorem Ipsum is simply dummy text of the printing and typesetting industry.</b> Lorem Ipsum has been the industry's standard dummy text ever since the 1500s, when an unknown printer took a galley of type and scrambled it to make a type specimen book. It has survived not only five centuries,</p>
  <p style="margin-top:14px">unchanged. It was popularised in the 1960s with the release of Presswell sheets containing Lorem Ipsum passages, and</p>
</div>
<h2 class="sec-title abs" style="left:81px;top:579px">Current &amp; Upcoming <b>Auctions</b></h2>

<article class="auction abs" style="top:604px;height:215px">
  <div class="bar">MARLOW FAMILY CLINIC IN ASHGROVE, NH</div>
  <div class="thumb" role="img" aria-label="Photo of a large shingled house"></div>
  <div class="info"><h4>Tate Ferrin Auctions, LLC NHL 4812 - Everything sold to the high bidder</h4>Location:<br>Location 1 - 412 Orchard Ridge Rd<br>Location 2 - 18 Mill Pond Ln # 3<br>Ashgrove, NH 03301</div>
  <div class="btn details"><svg width="18" height="18" viewBox="0 0 18 18"><circle cx="7" cy="7" r="5.5" fill="none" stroke="#fff" stroke-width="2"/><path d="M11 11l5 5" stroke="#fff" stroke-width="2.5"/></svg>DETAILS</div>
  <div class="btn photos"><svg width="22" height="15" viewBox="0 0 22 15"><rect x="1" y="2" width="20" height="12" rx="1.5" fill="#fff"/><circle cx="12" cy="8" r="3.5" fill="#1b2a78"/></svg>PHOTOS</div>
  <div class="dates"><b>Online Bidding Only</b>Began:&nbsp; Friday, May 24, 2013 at 10:06 AM EDT<br>Ends:&nbsp; Wednesday, June 05, 2013 at 10:00 AM EDT</div>
</article>
<article class="auction abs" style="top:839px;height:217px">
  <div class="bar">MARLOW FAMILY CLINIC IN ASHGROVE, NH</div>
  <div class="thumb" style="left:18px" role="img" aria-label="Photo of a large shingled house"></div>
  <div class="info" style="left:154px"><h4>Tate Ferrin Auctions, LLC NHL 4812 - Everything sold to the high bidder</h4>Location:<br>Location 1 - 412 Orchard Ridge Rd<br>Location 2 - 18 Mill Pond Ln # 3<br>Ashgrove, NH 03301</div>
  <div class="btn details" style="left:17px"><svg width="18" height="18" viewBox="0 0 18 18"><circle cx="7" cy="7" r="5.5" fill="none" stroke="#fff" stroke-width="2"/><path d="M11 11l5 5" stroke="#fff" stroke-width="2.5"/></svg>DETAILS</div>
  <div class="btn photos" style="left:17px"><svg width="22" height="15" viewBox="0 0 22 15"><rect x="1" y="2" width="20" height="12" rx="1.5" fill="#fff"/><circle cx="12" cy="8" r="3.5" fill="#1b2a78"/></svg>PHOTOS</div>
  <div class="dates" style="left:156px"><b>Online Bidding Only</b>Began:&nbsp; Friday, May 24, 2013 at 10:06 AM EDT<br>Ends:&nbsp; Wednesday, June 05, 2013 at 10:00 AM EDT</div>
</article>

<h2 class="sec-title abs" style="left:645px;top:446px">Watch <b>Video</b></h2>
<div class="video abs">
  <div class="play"><svg width="53" height="38" viewBox="0 0 53 38"><path d="M20 9l16 10-16 10z" fill="#fff"/></svg></div>
  <div class="ctrl"><span>▶ &nbsp; 00:00</span><span>00:00 &nbsp; ◂ ▮▮▮</span></div>
</div>
<aside class="side-box featured abs" style="top:637px;height:270px">
  <div class="bar">Featured Auctions</div>
  <p class="red" style="margin-top:14px;font-weight:700">Session 1 : Multi Estate &amp; Consignment<br>Auction</p>
  <div class="thumb" role="img" aria-label="Photo of a two-storey estate home"></div>
  <p><span class="red">Start Date / Time :</span> wedneday,<br>Aprail 10,2013 at 2pm</p>
  <p style="margin-top:8px"><span class="red">Location :</span> 1190 Kestrel Way,<br>Dunmore, NH 03824</p>
</aside>
<aside class="side-box testi abs" style="top:916px;height:140px">
  <div class="bar">CLIENT TESTIMONIALS</div>
  <blockquote><span style="position:absolute;left:11px;top:10px;font-weight:700">“</span>Lorem Ipsum is simply dummy text of the printing and typesetting industry.<span style="position:absolute;right:22px;top:30px;font-weight:700">”</span></blockquote>
  <p class="red" style="font-size:9.5px;font-weight:700;margin:14px 0 0 93px">Mr Alden Whitcombe</p>
</aside>

<footer class="footer abs">
  <h5>CONTACT INFO</h5>
  <address>Brookhollow Auctioneers<br>88 Granite Street • Concord, NH 03301<br>P: 555-014-3381 • F: 555-014-3390<br>Email : info@brookhollow.example</address>
</footer>
<div class="badge-a abs"></div>
<div class="badge-b abs"></div>
<div class="foot-brand abs"><span class="brand-mark"></span><span class="brand-name">BROOKHOLLOW</span></div>
<div class="copy abs">Copyright (C) Brookhollow Auctioneers 2013 - 2014 .&nbsp; All Rights Reserved</div>
</body>
</html>
```